Blue Harbor Inc - Cutting-Edge Biotech Laboratory - Sleek & Sophisticated

Please design a website that has more of a high-tech and high-end feel, with contents outlined in the uploaded file.

Please have main tabs of the following categories: Home, About, FDA & LAWS, Science, Products, Media, Contact.

Media can include all the videos and photos.

Current website: www.blueharborlabs.com - it needs to be much more high-end, sleek and more organized. Please do NOT follow the outlines in the old website, but follow the uploaded CONTENT file.

Target Market(s)

doctors

Industry/Entity Type

Biotechnology

Coding

Coded - Design and coding required

Number of Pages Required

5+ page

Requirements
Must have
• Logo
Nice to have
• Some lotion on the website

```html
<!DOCTYPE html>
<html lang="en">
<head>
<meta charset="utf-8">
<title>Blue Harbor Inc — Regenerative Medicine</title>
<link rel="stylesheet" href="https://fonts.googleapis.com/css2?family=Roboto:wght@300;400;500&display=swap">
<style>
  :root {
    --page-bg: #ffffff;
    --accent-blue: #1f5fbf;
    --brand-gold: #f2a81d;
    --nav-ink: #1d2433;
    --hero-deep: #060d1c;
    --hero-mid: #12294b;
    --hero-glow: #3f6fa3;
    --hero-ink: #ffffff;
    --section-label: #7d8aa6;
    --heading-ink: #28325a;
    --body-ink: #6a7390;
    --photo-light: #eef0f2;
    --photo-mid: #c9cfd6;
  }
  * { box-sizing: border-box; margin: 0; padding: 0; }
  html, body {
    width: 1200px;
    height: 676px;
    overflow: hidden;
    background: var(--page-bg);
    font-family: "Roboto", Arial, sans-serif;
  }
  .site {
    position: relative;
    width: 1200px;
    height: 676px;
    overflow: hidden;
  }

  /* Header */
  .site-header {
    height: 64px;
    border-top: 3px solid var(--accent-blue);
    display: flex;
    align-items: center;
    justify-content: space-between;
    padding: 0 60px 0 50px;
    background: var(--page-bg);
  }
  .brand {
    display: flex;
    align-items: center;
    gap: 10px;
    font-size: 17px;
    font-weight: 500;
    letter-spacing: 0.5px;
    color: var(--accent-blue);
    text-transform: uppercase;
  }
  .brand-dot {
    width: 26px;
    height: 26px;
    border-radius: 50%;
    background: var(--brand-gold);
  }
  .main-nav {
    display: flex;
    gap: 34px;
    list-style: none;
  }
  .main-nav a {
    font-size: 12px;
    color: var(--nav-ink);
    text-decoration: none;
    text-transform: uppercase;
  }

  /* Hero */
  .hero {
    position: relative;
    height: 426px;
  }
  .hero-visual {
    position: absolute;
    inset: 0;
    background:
      radial-gradient(ellipse 55% 35% at 72% 40%, rgba(63,111,163,0.75), transparent 70%),
      linear-gradient(160deg, var(--hero-deep) 0%, var(--hero-mid) 55%, var(--hero-deep) 100%);
  }
  .hero-content {
    position: relative;
    padding: 108px 0 0 55px;
    color: var(--hero-ink);
  }
  .hero-title {
    font-size: 28px;
    font-weight: 400;
    line-height: 1.22;
  }
  .hero-title span { display: block; }
  .hero-lead {
    margin-top: 26px;
    font-size: 16px;
    font-weight: 300;
    line-height: 1.15;
    width: 300px;
  }
  .hero-button {
    display: inline-block;
    margin-top: 26px;
    padding: 9px 20px;
    border: 2px solid var(--hero-ink);
    border-radius: 20px;
    font-size: 13px;
    color: var(--hero-ink);
    text-decoration: none;
  }

  /* About */
  .about {
    position: relative;
    height: 186px;
    padding: 32px 0 0 90px;
  }
  .section-label {
    font-size: 15px;
    font-weight: 300;
    color: var(--section-label);
  }
  .section-title {
    margin-top: 8px;
    font-size: 27px;
    font-weight: 400;
    color: var(--heading-ink);
  }
  .about-text {
    margin-top: 16px;
    width: 470px;
    font-size: 12px;
    line-height: 1.55;
    color: var(--body-ink);
  }
  .about-photo {
    position: absolute;
    left: 640px;
    top: 52px;
    width: 330px;
    height: 134px;
    background: linear-gradient(180deg, var(--photo-light) 0%, var(--photo-mid) 100%);
  }
</style>
</head>
<body>
<div class="site">
  <header class="site-header">
    <div class="brand"><span class="brand-dot"></span>Blue Harbor</div>
    <ul class="main-nav">
      <li><a href="#">About Us</a></li>
      <li><a href="#">FDA &amp; Laws</a></li>
      <li><a href="#">Science</a></li>
      <li><a href="#">Products</a></li>
      <li><a href="#">Media</a></li>
      <li><a href="#">Contact Us</a></li>
    </ul>
  </header>

  <section class="hero">
    <div class="hero-visual" role="img" aria-label="Glowing blue network of connected points on a dark navy background"></div>
    <div class="hero-content">
      <h1 class="hero-title">
        <span>Leader in Regenerative Medicine</span>
        <span>Innovator of the Industry</span>
        <span>Never Compromises on Quality</span>
      </h1>
      <p class="hero-lead">Interview with Blue Harbor chief scientist Marco Villena on stem cells</p>
      <a class="hero-button" href="#">Watch Interview</a>
    </div>
  </section>

  <section class="about">
    <p class="section-label">About Us</p>
    <h2 class="section-title">Who we are ?</h2>
    <p class="about-text">Blue Harbor Cell Shot Therapy provides Embryonic Stem Cells and unique protocols to doctors in order to help their patients who face major health conditions as well as individuals who simply wish to stay young and healthy.</p>
    <div class="about-photo" role="img" aria-label="Photo of a team of doctors talking together in a bright clinic"></div>
  </section>
</div>
</body>
</html>
```